Wordpress Website - for cutting edge Artificial Intelligence company

We need a wordpress web site for our company Varlomex.

Objective:
- To promote our software products to potential customers (e.g. large corporations)
- To promote our software products to potential partners (e.g. software makers who want to bundle our software inside their products)
- To promote our company to potential Investors (venture capital funds, angel investors, etc.)

Sample content and proposed structure can be found in the attached file.
Company logo is also attached.

The Plover logo should only be used in the section relating to the Plover Product (e.g. Plover Text & Plover Speech)

Target Market(s)

Core Target Market:
- Large corporations (e.g. Major Banks, Retailers & Pharmaceutical companies) who could buy our software

Industry/Entity Type

Software

Coding

Coded - Design and coding required

Font styles to use
Sans Serif

Colors
ffffff
ec1f27
000000
757575
dfdfdf
9bcb3c

Requirements
Must have
• Functionality:
• - Designed in Wordpress (using tools from wordpress.org, not hosted on wordpress.com)
• - Must have a user friendly CMS module for us to make updates easily
• - Must be designed to look great across different devices
• - Must be designed to look great in English and Chinese (as well as other future languages).

```html
<!DOCTYPE html>
<html lang="en">
<head>
<meta charset="utf-8">
<title>Varlomex</title>
<link rel="stylesheet" href="https://fonts.googleapis.com/css2?family=Open+Sans:ital,wght@0,400;0,600;0,700;1,400;1,600&display=swap">
<style>
:root{
  --red:#ec1f27;
  --black:#000000;
  --ink:#222222;
  --grey:#757575;
  --light:#dfdfdf;
  --paper:#ffffff;
  --frame:#e6e6e6;
  --footer:#141414;
  --bar:#1c1a1a;
}
*{box-sizing:border-box;margin:0;padding:0}
html,body{width:1200px;height:2161px;overflow:hidden}
body{background:var(--frame);font-family:"Open Sans",Arial,sans-serif;color:var(--ink);position:relative}
.page{position:absolute;left:14px;top:14px;width:1172px;height:2133px;background:var(--paper);overflow:hidden}
.abs{position:absolute}

/* header */
.topbar{left:562px;top:0;width:610px;height:44px;background:#f1f1f1;clip-path:polygon(14px 0,100% 0,100% 100%,0 100%)}
.top-mail{left:598px;top:12px;font-size:14px;color:#444;display:flex;align-items:center;gap:8px}
.social{display:flex;gap:3px}
.social span{width:19px;height:19px;border-radius:50%;border:2px solid var(--red);display:block}
.top-social{left:771px;top:12px}
.search{left:862px;top:8px;width:204px;height:28px;border:2px solid #555;border-radius:14px;font-size:13px;color:#555;padding:3px 14px}
.search svg{position:absolute;right:10px;top:5px}
.lang{left:1096px;top:13px;font-size:11px;color:#666}
.lang b{color:var(--red);font-weight:600}
.brand{left:29px;top:46px;font-size:50px;font-weight:700;color:var(--red);letter-spacing:1px;line-height:1}
.nav{left:408px;top:82px;display:flex;gap:22px;font-size:12.5px;font-weight:700;color:#222;letter-spacing:.2px}
.nav .on{color:var(--red)}
.nav .dd::after{content:"";display:inline-block;width:5px;height:5px;border-right:1.5px solid #444;border-bottom:1.5px solid #444;transform:rotate(45deg);margin:0 0 3px 5px}

/* hero */
.hero{left:0;top:124px;width:1172px;height:463px;background:radial-gradient(ellipse at 45% 45%,#3fc4f0 0%,#0f7fc2 35%,#0a4f8a 70%,#062f57 100%)}
.hero-name{left:358px;top:208px;font-size:60px;font-weight:600;color:#fff;letter-spacing:1px}
.hero-line{left:358px;top:284px;font-size:25px;font-weight:600;color:#fff;text-shadow:0 2px 4px rgba(0,0,0,.5)}
.dots{left:523px;top:447px;display:flex;gap:6px}
.dots span{width:27px;height:4px;background:#fff;display:block}
.dots span:first-child{background:var(--red)}
.cta{left:0;top:587px;width:1172px;height:92px;background:linear-gradient(#2a2727,#151313)}
.cta-item{top:30px;display:flex;align-items:center;gap:12px;font-size:19px;font-weight:600;color:#fff}
.cta-divider{left:588px;top:12px;width:1px;height:68px;background:#4a4646}

/* news */
.card{width:355px;height:315px;background:var(--black);box-shadow:0 8px 8px -4px rgba(0,0,0,.35)}
.card-media{width:355px;height:177px;display:block}
.card h3{position:absolute;left:16px;top:191px;font-size:14px;font-weight:700;color:#fff}
.card p{position:absolute;left:16px;top:214px;width:330px;font-size:12px;line-height:17px;color:#fff}
.more{position:absolute;right:0;bottom:0;width:111px;height:36px;background:var(--red);color:#fff;font-size:12.5px;padding:9px 0 0 12px}
.more::after{content:"";position:absolute;right:14px;top:15px;width:6px;height:6px;border-right:1.5px solid #fff;border-top:1.5px solid #fff;transform:rotate(45deg)}

/* stories */
.stories{left:0;top:1434px;width:1172px;height:425px;background:linear-gradient(135deg,#ececec 0%,#f6f6f6 35%,#e4e4e4 60%,#f4f4f4 100%)}
.stories h2{position:absolute;left:0;width:1172px;top:72px;text-align:center;font-size:24px;font-weight:700;color:#333}
.stories h2 em{font-style:normal;color:var(--red)}
.rule{top:88px;height:1px;background:#c9c9c9;width:160px}
.person{width:330px;text-align:center}
.avatar{width:94px;height:94px;border-radius:50%;border:3px solid var(--red);margin:0 auto;background:radial-gradient(circle,#f3d9c6,#b99481 70%,#fff 71%)}
.person h4{font-size:16px;font-style:italic;font-weight:600;color:#222;margin-top:22px}
.quote{position:relative;margin:26px auto 0;width:226px;text-align:left;font-size:13.5px;line-height:19px;color:#444}
.qmark{position:absolute;font-size:56px;font-weight:700;color:#333;line-height:1;font-family:Georgia,serif}

/* footer */
.footer{left:0;top:1859px;width:1172px;height:242px;background:var(--footer);color:#bbb}
.footer-brand{left:66px;top:98px;font-size:38px;font-weight:700;color:var(--red);letter-spacing:1px}
.footer h5{position:absolute;top:40px;font-size:14px;font-weight:700;color:#fff}
.links{left:379px;top:69px;list-style:none;font-size:12px;line-height:17px;font-weight:600;color:#ccc}
.contact-row{display:flex;gap:12px;font-size:12px;line-height:17px;font-weight:600;color:#ccc}
.about{left:832px;top:69px;width:275px;font-size:11.5px;line-height:16.5px;color:#8a8a8a}
.bottom{left:0;top:2101px;width:1172px;height:32px;background:#fff}
.copy{left:30px;top:9px;font-size:10px;font-weight:700;color:#555}
.bottom .social{position:absolute;right:26px;top:8px;gap:8px}
.bottom .social span{width:14px;height:14px;border:none;background:var(--red)}
</style>
</head>
<body>
<div class="page">

  <header>
    <div class="abs topbar"></div>
    <div class="abs top-mail">
      <svg width="18" height="18" viewBox="0 0 18 18"><circle cx="9" cy="9" r="8" fill="none" stroke="#ec1f27" stroke-width="2"/><rect x="5" y="6" width="8" height="6" fill="#ec1f27"/></svg>
      info@varlomex.com
    </div>
    <div class="abs social top-social"><span></span><span></span><span></span></div>
    <div class="abs search">Search
      <svg width="16" height="16" viewBox="0 0 16 16"><circle cx="6.5" cy="6.5" r="5" fill="none" stroke="#444" stroke-width="2"/><line x1="10" y1="10" x2="14.5" y2="14.5" stroke="#444" stroke-width="2"/></svg>
    </div>
    <div class="abs lang"><b>EN</b> &nbsp;|&nbsp; CH</div>
    <div class="abs brand">VARLOMEX</div>
    <nav class="abs nav">
      <span class="on">HOME</span>
      <span class="dd">NATURAL INTELLIGENCE</span>
      <span class="dd">PRODUCTS</span>
      <span class="dd">SERVICES</span>
      <span class="dd">PARTNERS</span>
      <span>CONTACT US</span>
      <span class="dd">ABOUT</span>
    </nav>
  </header>

  <section class="abs hero" role="img" aria-label="Blue circuit board background with glowing traces">
    <div class="abs hero-name">Plover</div>
    <div class="abs hero-line">The new standard in contact center customer experience.</div>
    <div class="abs dots"><span></span><span></span><span></span><span></span></div>
  </section>

  <section class="abs cta">
    <div class="abs cta-item" style="left:310px">
      <svg width="46" height="40" viewBox="0 0 46 40"><circle cx="18" cy="18" r="13" fill="none" stroke="#ec1f27" stroke-width="3"/><circle cx="18" cy="18" r="5" fill="#ec1f27"/><line x1="28" y1="28" x2="40" y2="38" stroke="#ec1f27" stroke-width="4"/></svg>
      REQUEST A DEMO
    </div>
    <div class="abs cta-divider"></div>
    <div class="abs cta-item" style="left:638px">
      <svg width="34" height="46" viewBox="0 0 34 46"><path d="M12 44 L8 30 Q6 25 10 24 L12 26 L12 10 Q12 6 15 6 Q18 6 18 10 L18 22 L26 24 Q30 25 29 30 L26 44" fill="none" stroke="#ec1f27" stroke-width="2.5"/><path d="M8 10 Q8 2 15 2 Q22 2 22 10" fill="none" stroke="#ec1f27" stroke-width="2"/></svg>
      CONTACT US
    </div>
  </section>

  <section class="news">
    <article class="abs card" style="left:35px;top:734px">
      <div class="card-media" role="img" aria-label="Businesswoman leaping among floating charts" style="background:linear-gradient(135deg,#e8edf2,#b9c3cf 60%,#8f98a8)"></div>
      <h3>News Title #1</h3>
      <p>Lorem ipsum dolor sit amet, consectetuer adipiscing elit, sed diam nonummy nibh euismod tincidunt ut laoreet dolore magna aliquam erat volutpat.</p>
      <span class="more">READ MORE</span>
    </article>
    <article class="abs card" style="left:408px;top:734px">
      <div class="card-media" role="img" aria-label="Glowing blue circuit board with chip" style="background:radial-gradient(circle at 50% 45%,#4fa3e8,#14399a 55%,#040c2c)"></div>
      <h3>News Title #2</h3>
      <p>Lorem ipsum dolor sit amet, consectetuer adipiscing elit, sed diam nonummy nibh euismod tincidunt ut laoreet dolore magna aliquam erat volutpat.</p>
      <span class="more">READ MORE</span>
    </article>
    <article class="abs card" style="left:783px;top:734px">
      <div class="card-media" role="img" aria-label="Hand touching a tablet showing a line chart" style="background:linear-gradient(135deg,#f6f6f6,#dcdcdc 60%,#3a3a3a)"></div>
      <h3>News Title #3</h3>
      <p>Lorem ipsum dolor sit amet, consectetuer adipiscing elit, sed diam nonummy nibh euismod tincidunt ut laoreet dolore magna aliquam erat volutpat.</p>
      <span class="more">READ MORE</span>
    </article>
    <article class="abs card" style="left:35px;top:1066px">
      <div class="card-media" role="img" aria-label="Hands holding a smartphone" style="background:linear-gradient(135deg,#2e4a7a,#8fa3c2 55%,#d9dee6)"></div>
      <h3>News Title #4</h3>
      <p>Lorem ipsum dolor sit amet, consectetuer adipiscing elit, sed diam nonummy nibh euismod tincidunt ut laoreet dolore magna aliquam erat volutpat.</p>
      <span class="more">READ MORE</span>
    </article>
    <article class="abs card" style="left:408px;top:1066px">
      <div class="card-media" role="img" aria-label="Team meeting around a laptop in a bright office" style="background:linear-gradient(135deg,#d8dde3,#a7b3c2 50%,#5b6878)"></div>
      <h3>News Title #5</h3>
      <p>Lorem ipsum dolor sit amet, consectetuer adipiscing elit, sed diam nonummy nibh euismod tincidunt ut laoreet dolore magna aliquam erat volutpat.</p>
      <span class="more">READ MORE</span>
    </article>
    <article class="abs card" style="left:783px;top:1066px">
      <div class="card-media" role="img" aria-label="Business people assembling large puzzle pieces" style="background:linear-gradient(135deg,#f4f4f4,#d4d4d4 60%,#9a9a9a)"></div>
      <h3>News Title #6</h3>
      <p>Lorem ipsum dolor sit amet, consectetuer adipiscing elit, sed diam nonummy nibh euismod tincidunt ut laoreet dolore magna aliquam erat volutpat.</p>
      <span class="more">READ MORE</span>
    </article>
  </section>

  <section class="abs stories">
    <div class="abs rule" style="left:182px"></div>
    <div class="abs rule" style="left:830px"></div>
    <h2><em>SUCCESS STORIES</em> FROM OUR PARTNERS</h2>

    <div class="abs person" style="left:70px;top:139px">
      <div class="avatar" role="img" aria-label="Portrait of Marina Ostrava"></div>
      <h4>Marina Ostrava</h4>
      <div class="quote"><span class="qmark" style="left:-40px;top:-8px">&#8220;</span>Lorem ipsum dolor sit amet, consec adipiscing elit, sed diam nonummy euismod tincidunt ut laoreet dolor aliquam erat volu ad veniam.<span class="qmark" style="right:-28px;bottom:-40px">&#8221;</span></div>
    </div>
    <div class="abs person" style="left:421px;top:139px">
      <div class="avatar" role="img" aria-label="Portrait of Elise Carrow"></div>
      <h4>Elise Carrow</h4>
      <div class="quote"><span class="qmark" style="left:-40px;top:-8px">&#8220;</span>Lorem ipsum dolor sit amet, consec adipiscing elit, sed diam nonummy euismod tincidunt ut laoreet dolor aliquam erat volu ad veniam.<span class="qmark" style="right:-28px;bottom:-40px">&#8221;</span></div>
    </div>
    <div class="abs person" style="left:772px;top:139px">
      <div class="avatar" role="img" aria-label="Portrait of Daniel Pruett"></div>
      <h4>Daniel Pruett</h4>
      <div class="quote"><span class="qmark" style="left:-40px;top:-8px">&#8220;</span>Lorem ipsum dolor sit amet, consec adipiscing elit, sed diam nonummy euismod tincidunt ut laoreet dolor aliquam erat volu ad veniam.<span class="qmark" style="right:-28px;bottom:-40px">&#8221;</span></div>
    </div>
  </section>

  <footer class="abs footer">
    <div class="abs footer-brand">VARLOMEX</div>
    <h5 style="left:379px">QUICK LINKS</h5>
    <ul class="abs links">
      <li>Home</li><li>Natural Intelligence</li><li>Products</li><li>Services</li><li>Partners</li><li>Contact Us</li><li>About</li>
    </ul>
    <h5 style="left:570px">CONTACT</h5>
    <div class="abs contact-row" style="left:566px;top:66px">
      <svg width="30" height="30" viewBox="0 0 30 30"><circle cx="15" cy="15" r="13.5" fill="none" stroke="#999" stroke-width="1.5"/><path d="M15 23 L10 15 A5.5 5.5 0 1 1 20 15 Z" fill="#999"/><circle cx="15" cy="12.5" r="2" fill="#141414"/></svg>
      <div>Varlomex Canada Corp.<br>18 Alder Lane, #402<br>Northbrook, ON &nbsp;Canada K2P 7L1</div>
    </div>
    <div class="abs contact-row" style="left:566px;top:144px;align-items:center">
      <svg width="30" height="30" viewBox="0 0 30 30"><circle cx="15" cy="15" r="13.5" fill="none" stroke="#999" stroke-width="1.5"/><rect x="8.5" y="10" width="13" height="10" fill="none" stroke="#999" stroke-width="1.5"/><path d="M8.5 10 L15 16 L21.5 10" fill="none" stroke="#999" stroke-width="1.5"/></svg>
      <div>info@varlomex.com</div>
    </div>
    <h5 style="left:832px">ABOUT VARLOMEX</h5>
    <p class="abs about">Lorem ipsum dolor sit amet, consectetuer adipis cing elit, sed diam nonummy nibh euismod tinci dunt ut laoreet dolore magna aliquam erat volut pat. Ut wisi enim ad minim veniam, quis nostrud exerci tation ullam corper suscipit lobortis nisl ut aliquip ex ea commodo consequat. Duis aut em vel eum iriure dolor in hendrerit in vulputa te velit esse molestie consequat, vel illum.</p>
  </footer>

  <div class="abs bottom">
    <div class="abs copy">COPYRIGHT © 2016 VARLOMEX CANADA CORP. ALL RIGHTS RESERVED.</div>
    <div class="social"><span></span><span></span><span></span></div>
  </div>

</div>
</body>
</html>
```